Mobile Fitness snd Therapy Business Card Design

I need a business card designed for my mobile fitness and therapy business.

Please view the images that I have uploaded. I like the simplicity of the design that I have attached. I adapted it with my information

Target Market(s)

Those seeking personal training, injury rehabilitation or massage therapy.

Industry/Entity Type

Business

Contact Information for Business Card

Derek Fulham - MSc, CAT(C), RMT, CSCS, Pn2
e-mail: derek@vantrelo.com
website: www.vantrelo.com
instagram: @derek_fulham

Font styles to use
Sans Serif

Colors
3176b5
0355a3

Requirements
Must have
• "Contact us to receive a FREE assessment"
• Services offered:
• Personal Training
• Golf Fitness
• Injury Rehab
• Massage Therapy
• Yoga
Nice to have
• Consistent colours with brand
• - Dark Blue: #232837
• - Blue: #5096f0
• Consistent look/feel with the website: www.vantrelo.com

```html
<!DOCTYPE html>
<html lang="en">
<head>
<meta charset="utf-8">
<title>Vantrelo Business Card</title>
<link rel="stylesheet" href="https://fonts.googleapis.com/css2?family=Roboto:wght@400;500;700&family=Roboto+Condensed:wght@500;700&display=swap">
<style>
  :root {
    --page-bg: #e9e9ec;
    --card-white: #f4f4f4;
    --navy: #232837;
    --blue: #2f5fd6;
    --blue-light: #5096f0;
    --text-grey: #4a4d55;
    --divider: #b9bbc0;
    --white: #ffffff;
  }
  * { margin: 0; padding: 0; box-sizing: border-box; }
  html, body { width: 1200px; height: 960px; overflow: hidden; }
  body { background: var(--page-bg); font-family: "Roboto", Arial, sans-serif; position: relative; }

  .card { position: absolute; width: 600px; height: 343px; border-radius: 22px; overflow: hidden; }
  .card-front { left: 314px; top: 113px; background: var(--card-white); box-shadow: 0 4px 10px rgba(0,0,0,.18); }
  .card-back { left: 311px; top: 472px; background: var(--navy); box-shadow: 0 4px 10px rgba(0,0,0,.25); }

  .brand { position: absolute; text-align: center; }
  .brand-name { font-family: "Roboto", Arial, sans-serif; font-weight: 700; letter-spacing: 4px; line-height: 1; }
  .brand-tagline { font-family: "Roboto", Arial, sans-serif; font-weight: 700; letter-spacing: 2px; line-height: 1; }

  .card-front .brand { left: 60px; top: 138px; width: 250px; }
  .card-front .brand-name { font-size: 33px; color: var(--navy); }
  .card-front .brand-tagline { font-size: 10.5px; color: var(--navy); margin-top: 8px; letter-spacing: 1.6px; }

  .divider { position: absolute; left: 332px; top: 102px; width: 1px; height: 114px; background: var(--divider); }

  .contact { position: absolute; left: 359px; top: 110px; }
  .person-name { font-family: "Roboto Condensed", Arial, sans-serif; font-weight: 700; font-size: 22px; color: var(--blue); line-height: 1; }
  .credentials { font-family: "Roboto Condensed", Arial, sans-serif; font-weight: 700; font-size: 10.5px; color: var(--blue); margin-top: 6px; }
  .contact-list { list-style: none; margin-top: 18px; }
  .contact-item { display: flex; align-items: center; gap: 8px; font-size: 14px; color: var(--text-grey); height: 19px; }
  .contact-item svg { width: 15px; height: 15px; flex: none; }

  .web-band { position: absolute; left: 94px; right: 0; top: 296px; height: 28px; background: var(--navy); color: var(--white); font-size: 14px; letter-spacing: 5px; text-align: center; line-height: 28px; padding-left: 20px; }

  .card-back .brand { left: 0; width: 600px; top: 128px; }
  .card-back .brand-name { font-size: 44px; color: var(--white); letter-spacing: 6px; }
  .card-back .brand-tagline { font-size: 15px; color: var(--white); margin-top: 12px; letter-spacing: 2.4px; }

  .cta { position: absolute; left: 59px; top: 259px; width: 482px; height: 32px; border-radius: 16px; background: var(--blue); color: var(--white); font-family: "Roboto Condensed", Arial, sans-serif; font-weight: 700; font-size: 20px; text-align: center; line-height: 32px; }
  .services { position: absolute; left: 0; width: 600px; top: 297px; text-align: center; color: var(--white); font-size: 14px; }
  .services .sep { color: var(--blue-light); margin: 0 3px; }
</style>
</head>
<body>
  <section class="card card-front">
    <div class="brand">
      <div class="brand-name">VANTRELO</div>
      <div class="brand-tagline">NUTRITION - FITNESS - HEALTH</div>
    </div>
    <div class="divider"></div>
    <div class="contact">
      <div class="person-name">DEREK FULHAM</div>
      <div class="credentials">MSC, CAT(C), RMT, CSCS, PN2</div>
      <ul class="contact-list">
        <li class="contact-item">
          <svg viewBox="0 0 16 16" aria-hidden="true"><rect x="2" y="4" width="12" height="9" rx="1" fill="var(--blue)"/><path d="M2.5 4.5 8 9l5.5-4.5" fill="none" stroke="var(--card-white)" stroke-width="1.2"/></svg>
          derek@vantrelo.com
        </li>
        <li class="contact-item">
          <svg viewBox="0 0 16 16" aria-hidden="true"><circle cx="8" cy="8" r="7" fill="var(--blue)"/><circle cx="8" cy="8" r="2.6" fill="none" stroke="var(--card-white)" stroke-width="1.3"/></svg>
          @derek_fulham
        </li>
      </ul>
    </div>
    <div class="web-band">www.vantrelo.com</div>
  </section>

  <section class="card card-back">
    <div class="brand">
      <div class="brand-name">VANTRELO</div>
      <div class="brand-tagline">NUTRITION - FITNESS - HEALTH</div>
    </div>
    <div class="cta">CONTACT US TO RECEIVE A FREE ASSESSMENT</div>
    <div class="services">Personal Training<span class="sep">|</span>Golf Fitness<span class="sep">|</span>Injury Rehab<span class="sep">|</span>Massage Therapy<span class="sep">|</span>Yoga</div>
  </section>
</body>
</html>
```